I need a business card design for a new dance business. I offer classical Indian dance tuition and also professional performances. I want to offer the community a variety of Indian dance experiences which include: group class and private tuition, school and preschool educational courses and workshops. dance theatre performances, community function workshops and performances, Kids Bollywood parties, wedding & conference performances, mouth percussion classes, Indian mythology/ dance costume and make up workshops.
The final design should communicate a feeling and impression of the vibrance and energy of Indian dance.
Updates
Hi Everyone,
Project Deadline Extended
Reason: I would like to refine a few changes to the details of this lovely design and we have run out of time!
Project Deadline Extended
Reason: Still waiting to hear back form designer re two possible changes to the card design. Tomorrow is the deadline and I have sent several messages but with no response. I need to see this through before selecting this lovely design.
Thank you.
Tara
Industry/Entity Type
Preschool
Requirements
Must have
- The front of the business card should have the photo of me (my face and torso), surrounded entirely by a border of bright magenta (to match the magenta of my lipstick - it is the same as the magenta on my skirt in the second photo). Within the top border I want (perhaps yellow-gold) writing to say "Tara Holloway - Artistic Director" and within the bottom border it should read "Saffron Lantern Indian Dance." If you turn the card on its side the left border should have my telephone number: 0417 862 493 and the right-hand border should read: saffronlanternindiandance@quillmail.example
The reverse of the card should be the orange of the dance costume
and I'd like the picture of my feet and legs to be on the right side of the back of the card as a side border. Centre-aligned on the orange background it should read (perhaps in dark magenta):
Indian dance classes + private tuition
School + preschool educational courses and workshops
Dance theatre performances
Community function workshops and performances
Children's Bollywood parties
Wedding + conference performances
Mouth percussion classes
Indian mythology and dance demonstration workshops
Dance costume and make-up workshops
Nice to have
- A lovely artistic but easy-to-read font would be nice.

```html
<!DOCTYPE html>
<html lang="en">
<head>
<meta charset="utf-8">
<title>Saffron Lantern Indian Dance – Business Card</title>
<link rel="stylesheet" href="https://fonts.googleapis.com/css2?family=Amethysta&family=Open+Sans:wght@300;400&display=swap">
<style>
  :root {
    --saffron: #e07a2f;
    --saffron-clear: rgba(224,122,47,0);
    --magenta: #d62f93;
    --deep-magenta: #c0308a;
    --plum: #7a1a5a;
    --gold: #e3a04a;
    --white: #ffffff;
    --canvas: #ffffff;
  }
  * { box-sizing: border-box; margin: 0; padding: 0; }
  html, body { width: 1200px; height: 900px; overflow: hidden; background: var(--canvas); }
  .canvas { position: relative; width: 1200px; height: 900px; }

  .card { position: absolute; top: 88px; height: 764px; overflow: hidden; }

  /* Front */
  .card--front { left: 104px; width: 463px; background: var(--saffron); }
  .front__photo {
    position: absolute; left: 150px; top: 0; width: 313px; height: 681px;
    background: linear-gradient(100deg, var(--saffron-clear) 0%, #a8246f 22%, #8c1f5e 45%, #c58a3e 70%, #d9a054 85%, var(--plum) 100%);
  }
  /* soft saffron fade keeping the title area clear */
  .front__photo::after {
    content: ""; position: absolute; left: 0; top: 0; width: 100%; height: 100%;
    background: linear-gradient(90deg, var(--saffron) 0, var(--saffron) 115px, var(--saffron-clear) 175px);
    -webkit-mask-image: linear-gradient(180deg, transparent 0, transparent 48%, #000 60%, #000 100%);
    mask-image: linear-gradient(180deg, transparent 0, transparent 48%, #000 60%, #000 100%);
  }
  .front__title {
    position: absolute; left: 0; top: 425px; width: 258px; z-index: 1;
    font-family: "Amethysta", serif; font-weight: 400; font-size: 41px; line-height: 51px;
    color: var(--deep-magenta); text-align: center;
  }
  .front__name {
    position: absolute; left: 0; top: 636px; width: 262px; z-index: 1;
    font-family: "Amethysta", serif; font-size: 27px; color: var(--white); text-align: center;
  }
  .front__band {
    position: absolute; left: 0; bottom: 0; width: 100%; height: 83px;
    background: var(--magenta);
    display: flex; align-items: center; justify-content: center;
  }
  .front__phone {
    font-family: "Open Sans", sans-serif; font-weight: 300; font-size: 33px;
    color: var(--gold); letter-spacing: 1px;
  }

  /* Back */
  .card--back { left: 633px; width: 466px; background: var(--magenta); }
  .back__band {
    height: 87px; background: var(--saffron);
    display: flex; align-items: center; justify-content: center;
  }
  .back__email {
    font-family: "Amethysta", serif; font-size: 17.5px; color: var(--deep-magenta);
    letter-spacing: 0.4px; white-space: nowrap;
  }
  .services {
    list-style: none; margin-top: 23px; text-align: center;
    font-family: "Amethysta", serif; font-size: 15.5px; line-height: 18px; color: var(--white);
  }
  .services li { margin-bottom: 18px; }
  .back__photo {
    position: absolute; left: 48px; top: 500px; width: 396px; height: 264px;
    background: radial-gradient(ellipse at 50% 60%, #e5a53a 0%, #c98a3a 35%, rgba(214,47,147,0) 72%);
  }
</style>
</head>
<body>
<main class="canvas">
  <section class="card card--front">
    <div class="front__photo" role="img" aria-label="Photograph of a classical Indian dancer's leg and foot in a magenta and gold silk costume with ankle bells"></div>
    <h1 class="front__title">Saffron Lantern Indian Dance</h1>
    <p class="front__name">Tara Holloway</p>
    <div class="front__band"><span class="front__phone">0417 862 493</span></div>
  </section>

  <section class="card card--back">
    <div class="back__band"><span class="back__email">saffronlanternindiandance@quillmail.example</span></div>
    <ul class="services">
      <li>Indian dance classes + private tuition</li>
      <li>School + preschool educational courses<br>and workshops</li>
      <li>Dance theatre performances</li>
      <li>Community function&nbsp; workshops<br>and performances</li>
      <li>Children's Bollywood parties</li>
      <li>Wedding + conference performances</li>
      <li>Mouth percussion classes</li>
      <li>Indian mythology and dance demonstration<br>workshop</li>
      <li>Dance costume and make-up workshops</li>
    </ul>
    <div class="back__photo" role="img" aria-label="Photograph of the dancer in a gold and maroon costume with jewellery, hands raised in a classical pose"></div>
  </section>
</main>
</body>
</html>
```